Design and Renovation Company Luxury Business Card

I want to create a luxury business card for a Design and Renovation Firm . We will use our current logo. The company name is 528BUILDA. We do not want anything standard. We need a very unique concept.
Please see uploaded inspiration. I really like the textured paper option. I would like the card to be thick with debossing, and/or embossing options. The logo has orange in it but I would like to see the card with and without the orange. I think the orange may make the company feel less high-end. The goal is to elevate the logo not match its vibe per se of the logo. We want something very unique, not standard at all!
I would like a space for :
Logo,
Name,
Position,
Email,
Office number,
Website Address,
Business Address,
Thank you!
Have fun!
Target Market(s)
Home owners Age 35 +
Industry/Entity Type
Design and Renovation
Contact Information for Business Card
Logo, Name, Position, Email, Office number, Website Address, Business Address,.
Colors
Designer to choose colors to be used in the design.
Requirements
Must have
- A luxury designer feel. Must be black or dark grey but open to other luxury ideas.
Nice to have
- Gold, silver, black embossing or debossing. Textured paper design.
Should not have
- A cheap look and feel.

```html
<!DOCTYPE html>
<html lang="en">
<head>
<meta charset="utf-8">
<title>528BUILDA Business Card</title>
<link href="https://fonts.googleapis.com/css2?family=Montserrat:wght@400;500;700&display=swap" rel="stylesheet">
<style>
  :root {
    --backdrop: #e6e1d9;
    --card-white: #ffffff;
    --card-black: #151515;
    --ink: #111111;
    --ink-soft: #1c1c1c;
    --accent: #f39a1e;
    --panel-grey: #e7e7e7;
    --panel-warm: #fdf4ea;
    --deboss: #262626;
  }
  * { margin: 0; padding: 0; box-sizing: border-box; }
  html, body {
    width: 900px; height: 1200px; overflow: hidden;
    background: var(--backdrop);
    font-family: "Montserrat", sans-serif;
    color: var(--ink);
  }
  .canvas { position: relative; width: 900px; height: 1200px; }

  .card { position: absolute; border-radius: 24px; overflow: hidden; }
  .card--front { left: 80px; top: 130px; width: 742px; height: 442px; background: var(--card-white); }
  .card--back { left: 78px; top: 638px; width: 744px; height: 442px; background: var(--card-black); }

  .tile { position: absolute; width: 184px; }
  .tile--warm { left: 558px; top: 42px; height: 183px; background: var(--panel-warm); }
  .tile--grey-left { left: 341px; top: 258px; height: 184px; background: var(--panel-grey); }
  .tile--grey-right { left: 558px; top: 258px; height: 184px; background: var(--panel-grey); }

  .brand {
    position: absolute;
    font-weight: 500; letter-spacing: 3px; line-height: 1;
  }
  .card--front .brand { left: 44px; top: 70px; font-size: 46px; color: var(--ink); }
  .card--back .brand {
    left: 50%; top: 50%; transform: translate(-50%, -50%);
    font-size: 66px; color: var(--deboss);
  }

  .person { position: absolute; left: 34px; top: 258px; }
  .person__name { font-weight: 700; font-size: 27px; line-height: 1.1; color: var(--ink-soft); }
  .person__role { font-weight: 400; font-size: 16px; margin-top: 6px; color: var(--ink-soft); }

  .contacts { position: absolute; left: 34px; top: 331px; list-style: none; }
  .contacts li {
    display: flex; align-items: center; gap: 9px;
    font-size: 16px; height: 28.5px; color: var(--ink-soft);
  }
  .contacts svg { width: 16px; height: 16px; flex: none; }

  .address {
    position: absolute; left: 494px; top: 370px;
    font-size: 16px; line-height: 21px; font-style: normal; color: var(--ink-soft);
  }
</style>
</head>
<body>
<main class="canvas">
  <section class="card card--front" aria-label="Business card front">
    <div class="tile tile--warm"></div>
    <div class="tile tile--grey-left"></div>
    <div class="tile tile--grey-right"></div>

    <div class="brand">528BUILDA</div>

    <div class="person">
      <h1 class="person__name">Daniel Carter</h1>
      <p class="person__role">Managing Director</p>
    </div>

    <ul class="contacts">
      <li>
        <svg viewBox="0 0 16 16" aria-hidden="true"><path fill="#f39a1e" d="M3.6 1.5l2.2 2.6-1.2 1.7c.8 1.9 2.2 3.3 4 4.1l1.7-1.2 2.6 2.2-1.3 2.2C6.8 13.1 2.9 9.2 1.4 2.8z"/></svg>
        555-318-0247
      </li>
      <li>
        <svg viewBox="0 0 16 16" aria-hidden="true"><rect x="1.5" y="3.5" width="13" height="9" fill="#f39a1e"/><path d="M1.5 3.8L8 8.5l6.5-4.7" fill="none" stroke="#fff" stroke-width="1.2"/></svg>
        info@528builda.com
      </li>
      <li>
        <svg viewBox="0 0 16 16" aria-hidden="true"><circle cx="8" cy="8" r="6.8" fill="#f39a1e"/><path d="M1.5 8h13M8 1.2c-2.6 3.6-2.6 10 0 13.6M8 1.2c2.6 3.6 2.6 10 0 13.6" fill="none" stroke="#fff" stroke-width="1"/></svg>
        www.528builda.com
      </li>
    </ul>

    <address class="address">
      415 Maple Ridge Ave, #112<br>
      Brookfield, OH 430157
    </address>
  </section>

  <section class="card card--back" aria-label="Business card back">
    <div class="brand">528BUILDA</div>
  </section>
</main>
</body>
</html>
```